Birchline Septic Solutions

Would like to see some single sided ones but would also like to see some double sided with one sided only being the logo. Owners name is Colin Vandro. Phone number is 555-214-0387
Services are pumping, inspections, installs, and repairs

Contact Information for Business Card

555-241-0387 Colin Vandro Ridgeford, OH

```html
<!DOCTYPE html>
<html lang="en">
<head>
<meta charset="utf-8">
<title>Birchline Septic Solutions – Business Cards</title>
<link href="https://fonts.googleapis.com/css2?family=Archivo+Black&family=Montserrat:wght@500;700&display=swap" rel="stylesheet">
<style>
  :root {
    --backdrop: #a3a4a8;
    --card-white: #ffffff;
    --card-black: #111112;
    --ink: #141414;
    --paper-text: #f4f4f4;
    --teal: #3cbdb1;
    --scene-dark: #1f1f1f;
    --scene-light: #8a8a8a;
  }
  * { box-sizing: border-box; margin: 0; padding: 0; }
  html, body { width: 1200px; height: 876px; overflow: hidden; }
  body {
    background: var(--backdrop);
    display: flex;
    align-items: center;
    justify-content: center;
    gap: 48px;
    font-family: "Montserrat", sans-serif;
  }
  .card {
    width: 532px;
    height: 304px;
    position: relative;
    overflow: hidden;
    box-shadow: 0 10px 24px rgba(0,0,0,.25);
  }

  /* Front */
  .card--front { background: var(--card-white); color: var(--ink); }
  .front__scenery {
    position: absolute;
    left: 0;
    top: 112px;
    bottom: 0;
    width: 236px;
    background: linear-gradient(180deg, var(--scene-light) 0%, var(--scene-dark) 100%);
  }
  .front__brand {
    position: absolute;
    left: 28px; top: 28px;
    display: flex;
    align-items: center;
    gap: 8px;
  }
  .brand-mark {
    width: 12px; height: 12px;
    background: var(--teal);
    flex: none;
  }
  .brand-name {
    font-weight: 700;
    font-size: 15px;
    letter-spacing: .16em;
    text-transform: uppercase;
    line-height: 1.25;
    color: var(--ink);
  }
  .front__contact {
    position: absolute;
    right: 34px; top: 96px;
    width: 250px;
    text-align: right;
  }
  .person-name {
    font-family: "Archivo Black", sans-serif;
    font-weight: 400;
    font-size: 25px;
    letter-spacing: .06em;
    text-transform: uppercase;
    line-height: 1;
    white-space: nowrap;
  }
  .person-role {
    color: var(--teal);
    font-weight: 500;
    font-size: 15px;
    letter-spacing: .06em;
    margin-top: 6px;
  }
  .contact-list { list-style: none; margin-top: 18px; }
  .contact-list li {
    display: flex;
    justify-content: flex-end;
    align-items: center;
    gap: 8px;
    font-weight: 500;
    font-size: 15px;
    letter-spacing: .06em;
    margin-top: 6px;
    white-space: nowrap;
  }
  .contact-list svg { width: 14px; height: 14px; fill: var(--teal); flex: none; }

  /* Back */
  .card--back {
    background: var(--card-black);
    color: var(--paper-text);
    display: flex;
    flex-direction: column;
    align-items: center;
    justify-content: center;
  }
  .back__brand { display: flex; align-items: center; gap: 12px; }
  .back__brand .brand-mark { width: 16px; height: 16px; }
  .back__brand .brand-name { color: var(--paper-text); font-size: 24px; text-align: left; }
  .services {
    list-style: none;
    display: flex;
    gap: 10px;
    margin-top: 44px;
    font-weight: 500;
    font-size: 13px;
    letter-spacing: .14em;
    text-transform: uppercase;
    white-space: nowrap;
  }
  .services li + li::before {
    content: "|";
    color: var(--teal);
    margin-right: 10px;
  }
</style>
</head>
<body>
  <section class="card card--front" aria-label="Card front">
    <div class="front__scenery" role="img" aria-label="Black and white mountain peaks with pine tree silhouettes"></div>
    <div class="front__brand">
      <span class="brand-mark"></span>
      <span class="brand-name">Birchline<br>Septic Solutions</span>
    </div>
    <div class="front__contact">
      <h1 class="person-name">Colin Vandro</h1>
      <p class="person-role">Owner</p>
      <ul class="contact-list">
        <li>555-214-0387
          <svg viewBox="0 0 24 24" aria-hidden="true"><path d="M6.6 10.8a15.1 15.1 0 0 0 6.6 6.6l2.2-2.2a1 1 0 0 1 1-.25 11.4 11.4 0 0 0 3.6.57 1 1 0 0 1 1 1V20a1 1 0 0 1-1 1A17 17 0 0 1 3 4a1 1 0 0 1 1-1h3.5a1 1 0 0 1 1 1c0 1.25.2 2.45.57 3.57a1 1 0 0 1-.25 1z"/></svg>
        </li>
        <li>Ridgeford, OH
          <svg viewBox="0 0 24 24" aria-hidden="true"><path d="M12 2a7 7 0 0 0-7 7c0 5.2 7 13 7 13s7-7.8 7-13a7 7 0 0 0-7-7zm0 9.5A2.5 2.5 0 1 1 12 6.5a2.5 2.5 0 0 1 0 5z"/></svg>
        </li>
      </ul>
    </div>
  </section>

  <section class="card card--back" aria-label="Card back">
    <div class="back__brand">
      <span class="brand-mark"></span>
      <span class="brand-name">Birchline<br>Septic Solutions</span>
    </div>
    <ul class="services">
      <li>Pumping</li>
      <li>Inspections</li>
      <li>Installs</li>
      <li>Repairs</li>
    </ul>
  </section>
</body>
</html>
```